Board to put on a meditation centre - Lantern Grove

I need a board design for a new meditation centre based in Oslo which offers free courses in meditation and self-empowerment. The size of the board is width 374cm x height 104cm.  The name of the meditation centre together with subtitles should be on the board but also some elegant decoration that matches the theme (lantern grove/meditation).
Here is the website of the meditation centre to give you a feeling of it: https://kvitfjellsenteret.no/
Good if you can use a blue color close to this one: rgb(37, 180, 193) as well as some brown/golden color (similar to the palette on the website).
On the board it should say:
Kveldens lund (in big letters, the rest is subtitles)
Meditasjon & Spirituell visdom
Kurs - Retreat - Dialog
kvitfjellsenteret.no
The design should be very elegant and beautiful and the feeling should be of "A Lantern Grove". A logo is here attached and should be used but I need to get a better quality version of it, will upload that as soon as possible.

```html
<!DOCTYPE html>
<html lang="no">
<head>
<meta charset="utf-8">
<title>Kveldens lund – skilt</title>
<link rel="stylesheet" href="https://fonts.googleapis.com/css2?family=Marcellus&family=Montserrat:wght@800&family=Poppins:wght@500;600&display=swap">
<style>
  :root {
    --teal-deep: #0f7a86;
    --teal: #25b4c1;
    --teal-dark: #0b6d78;
    --sand: #bdb1a1;
    --gold: #c8b79d;
    --white: #ffffff;
    --page: #f4f4f3;
    --red: #e11d3f;
    --ink: #5a5a5a;
  }
  html, body {
    margin: 0;
    width: 1110px;
    height: 1200px;
    overflow: hidden;
    background: var(--page);
  }
  .canvas {
    position: relative;
    width: 1110px;
    height: 1200px;
  }
  .board {
    position: absolute;
    left: 55px;
    top: 461px;
    width: 1000px;
    height: 278px;
    box-shadow: 0 14px 30px rgba(0,0,0,0.18);
  }
  .board svg { display: block; }
  .title { font-family: "Marcellus", serif; fill: var(--white); }
  .subtitle { font-family: "Montserrat", sans-serif; font-weight: 800; fill: var(--white); }
  .offer { font-family: "Poppins", sans-serif; font-weight: 600; fill: var(--white); }
  .url { font-family: "Poppins", sans-serif; font-weight: 500; fill: var(--white); }
  .org-name { font-family: "Poppins", sans-serif; font-weight: 500; fill: var(--ink); }
</style>
</head>
<body>
<div class="canvas">
  <div class="board">
    <svg width="1000" height="278" viewBox="0 0 1000 278" xmlns="http://www.w3.org/2000/svg">
      <defs>
        <linearGradient id="tealFill" x1="0" y1="0" x2="1" y2="1">
          <stop offset="0" stop-color="var(--teal-deep)"/>
          <stop offset="1" stop-color="var(--teal)"/>
        </linearGradient>
        <radialGradient id="photoTone" cx="0.5" cy="0.55" r="0.6">
          <stop offset="0" stop-color="#d9c3b3"/>
          <stop offset="0.45" stop-color="#f0b3bd"/>
          <stop offset="1" stop-color="#f7e9eb"/>
        </radialGradient>
        <pattern id="dotGrid" width="8" height="8" patternUnits="userSpaceOnUse">
          <circle cx="4" cy="4" r="1.4" fill="var(--white)" opacity="0.9"/>
        </pattern>
      </defs>

      <!-- base -->
      <rect class="board-base" width="1000" height="278" fill="var(--white)"/>

      <!-- wave layers -->
      <path class="wave-sand" d="M0 0 H715 C660 30 670 90 735 150 C780 195 785 245 780 278 H0 Z" fill="var(--sand)"/>
      <path class="wave-dark" d="M0 0 H700 C648 28 655 88 718 150 C762 195 768 245 764 278 H0 Z" fill="var(--teal-dark)"/>
      <path class="wave-main" d="M0 0 H680 C628 30 640 90 700 150 C742 195 748 245 744 278 H0 Z" fill="url(#tealFill)"/>
      <path class="wave-line" d="M722 0 C675 32 690 95 752 152 C795 198 800 245 796 278" fill="none" stroke="var(--gold)" stroke-width="3"/>

      <!-- photo area -->
      <rect x="735" y="0" width="265" height="278" fill="url(#photoTone)" role="img" aria-label="Photo of a woman meditating in lotus pose in front of red radiating rays"/>
      <path d="M0 0 H700 C648 28 655 88 718 150 C762 195 768 245 764 278 H0 Z" fill="none"/>

      <!-- dot decorations -->
      <rect x="0" y="2" width="30" height="54" fill="url(#dotGrid)"/>
      <rect x="555" y="172" width="30" height="54" fill="url(#dotGrid)"/>

      <!-- headline -->
      <text class="title" x="56" y="120" font-size="96" textLength="540" lengthAdjust="spacingAndGlyphs">KVELDENS LUND</text>
      <text class="subtitle" x="57" y="153" font-size="27" textLength="535" lengthAdjust="spacingAndGlyphs">MEDITASJON &amp; SPIRITUELL VISDOM</text>

      <!-- offers -->
      <g class="icon-course" transform="translate(60,176)">
        <rect x="0" y="4" width="22" height="15" rx="2" fill="var(--white)"/>
        <rect x="3" y="7" width="16" height="8" fill="var(--teal-deep)"/>
        <rect x="-2" y="19" width="26" height="3" rx="1" fill="var(--white)"/>
      </g>
      <text class="offer" x="92" y="197" font-size="27">Kurs</text>

      <g class="icon-lotus" transform="translate(191,174)" fill="var(--white)">
        <path d="M16 24 C10 16 10 8 16 0 C22 8 22 16 16 24 Z"/>
        <path d="M14 24 C6 22 2 14 3 7 C9 10 13 16 14 24 Z"/>
        <path d="M18 24 C26 22 30 14 29 7 C23 10 19 16 18 24 Z"/>
        <path d="M12 25 C5 25 0 21 -2 16 C4 17 9 20 12 25 Z"/>
        <path d="M20 25 C27 25 32 21 34 16 C28 17 23 20 20 25 Z"/>
      </g>
      <text class="offer" x="234" y="197" font-size="27">Retreat</text>

      <g class="icon-dialog" transform="translate(377,174)">
        <path d="M0 2 H20 V16 H8 L3 21 V16 H0 Z" fill="var(--gold)"/>
        <path d="M23 8 H30 V22 H27 V27 L22 22 H12 V19 H23 Z" fill="var(--gold)"/>
        <rect x="4" y="6" width="12" height="2" fill="var(--teal-deep)"/>
        <rect x="4" y="10" width="9" height="2" fill="var(--teal-deep)"/>
      </g>
      <text class="offer" x="416" y="197" font-size="27">Dialog</text>

      <!-- footer tab -->
      <path class="org-tab" d="M0 221 H265 C295 221 305 250 318 278 H0 Z" fill="var(--white)"/>
      <circle cx="78" cy="250" r="13" fill="var(--red)"/>
      <text class="org-name" x="100" y="256" font-size="15" letter-spacing="1">Lysstien</text>

      <!-- url -->
      <g class="icon-web" transform="translate(331,249)">
        <circle r="10" fill="var(--white)"/>
        <circle r="6" fill="none" stroke="var(--teal-deep)" stroke-width="1.6"/>
        <path d="M-6 0 H6 M0 -6 V6" stroke="var(--teal-deep)" stroke-width="1.4"/>
      </g>
      <text class="url" x="348" y="257" font-size="23">kvitfjellsenteret.no</text>
    </svg>
  </div>
</div>
</body>
</html>
```